Appraisal and Umpire Services for Property Damage Insurance Claims

I need a banner design that I can post as an advertisement on industry web pages. I would like this to be elegant and reflective of quality, integrity and professionalism.

Target Market(s)

Insurance Companies and Attorneys

Industry/Entity Type

Insurance

Contact Information for Business Card

Gordon T. Ashby
218 Birchwell Lane
PO Box 913
Clifton Park, NY 12348
gashby@meridaleclaims.com
Phone: (800) 519-4867, Ext. 2716
Direct: (315) 648-9052

Logo Text

Line One: Silver Hollow Claim Service, Inc. Line two: Appraisal and Umpire Services

Font styles to use
Serif
Sans Serif

Colors
0255a3
f78f20
faa54b
3176b5

Requirements
Must have
• New Logo and matching banner, business card and stationary.
• The colors must be orange and navy blue in the logo. I have selected them below.

```html
<!DOCTYPE html>
<html lang="en">
<head>
<meta charset="utf-8">
<title>Silver Hollow Claim Service – Stationery</title>
<link href="https://fonts.googleapis.com/css2?family=Raleway:wght@400&family=Open+Sans:wght@400;700&display=swap" rel="stylesheet">
<style>
  :root {
    --backdrop: #e2e2e2;
    --paper: #ffffff;
    --orange: #f26a10;
    --navy: #0255a3;
    --ink: #3a3a3a;
    --ink-soft: #8a8a8a;
    --shadow: rgba(0, 0, 0, 0.14);
  }
  * { box-sizing: border-box; margin: 0; padding: 0; }
  html, body {
    width: 1200px; height: 640px; overflow: hidden;
    background: var(--backdrop);
    font-family: "Open Sans", Arial, sans-serif;
  }
  .canvas { position: relative; width: 1200px; height: 640px; }

  .sheet {
    position: absolute;
    background: var(--paper);
    box-shadow: 0 3px 10px var(--shadow);
  }

  /* Brand lockup: square mark + name in one colour and weight */
  .brand {
    position: absolute;
    display: flex; align-items: center; gap: 6px;
    font-family: "Raleway", Arial, sans-serif;
    font-weight: 400;
    color: var(--navy);
    white-space: nowrap;
  }
  .brand-mark { display: block; background: var(--orange); flex: none; }
  .brand-name { line-height: 1.15; }

  .contact {
    position: absolute;
    color: var(--ink-soft);
    line-height: 1.3;
  }
  .contact-title { color: var(--ink); font-weight: 700; }

  /* Letterhead, reverse sheet */
  .letterhead-back { left: 40px; top: 90px; width: 300px; height: 388px; }
  .letterhead-back .brand { left: 22px; bottom: 24px; font-size: 13px; }
  .letterhead-back .brand-mark { width: 14px; height: 14px; }

  /* Letterhead, front sheet */
  .letterhead-front { left: 370px; top: 90px; width: 300px; height: 388px; }
  .letterhead-front .brand { right: 20px; top: 22px; font-size: 13px; }
  .letterhead-front .brand-mark { width: 14px; height: 14px; }
  .letterhead-front .contact { right: 20px; bottom: 20px; font-size: 5px; width: 90px; }

  /* Envelope */
  .envelope { left: 720px; top: 60px; width: 420px; height: 162px; }
  .envelope .brand { right: 20px; top: 86px; font-size: 12px; }
  .envelope .brand-mark { width: 13px; height: 13px; }
  .envelope .contact { right: 20px; bottom: 14px; font-size: 5px; width: 90px; }

  /* Business card */
  .business-card { left: 780px; top: 320px; width: 350px; height: 200px; }
  .business-card .brand {
    left: 0; right: 0; top: 70px; justify-content: center;
    font-size: 20px; gap: 10px;
  }
  .business-card .brand-mark { width: 22px; height: 22px; }
  .business-card .contact { bottom: 14px; font-size: 10px; }
  .business-card .contact-person { left: 20px; }
  .business-card .contact-lines { left: 170px; }
</style>
</head>
<body>
<main class="canvas">

  <section class="sheet letterhead-back" aria-label="Letterhead reverse">
    <div class="brand">
      <span class="brand-mark"></span>
      <span class="brand-name">Silver Hollow Claim Service, Inc.</span>
    </div>
  </section>

  <section class="sheet letterhead-front" aria-label="Letterhead">
    <div class="brand">
      <span class="brand-mark"></span>
      <span class="brand-name">Silver Hollow Claim Service, Inc.</span>
    </div>
    <address class="contact">
      <div class="contact-title">Contact</div>
      <div>Gordon T. Ashby</div>
      <div>Email: gashby@meridaleclaims.com</div>
      <div>Phone: (800) 519-4867, Ext. 2716</div>
    </address>
  </section>

  <section class="sheet envelope" aria-label="Envelope">
    <div class="brand">
      <span class="brand-mark"></span>
      <span class="brand-name">Silver Hollow Claim Service, Inc.</span>
    </div>
    <address class="contact">
      <div class="contact-title">Contact</div>
      <div>Gordon T. Ashby</div>
      <div>Email: gashby@meridaleclaims.com</div>
      <div>Phone: (800) 519-4867, Ext. 2716</div>
    </address>
  </section>

  <section class="sheet business-card" aria-label="Business card">
    <div class="brand">
      <span class="brand-mark"></span>
      <span class="brand-name">Silver Hollow Claim Service, Inc.</span>
    </div>
    <address class="contact contact-person">
      <div class="contact-title">Contact</div>
      <div>Gordon T. Ashby</div>
    </address>
    <address class="contact contact-lines">
      <div>Email: gashby@meridaleclaims.com</div>
      <div>Phone: (800) 519-4867, Ext. 2716</div>
    </address>
  </section>

</main>
</body>
</html>
```